Parcelwise HQ letterhead and envelope

Design a formal (8.5x11) letterhead and envelope for sales outreach and legal matters. Using design input from https://www.parcelwisehq.example/ and the attached documents.

Industry/Entity Type

Software Service

Requirements
Must have
• These 4 hex colors are our official colors:
• #355c98 [blue]
• #1eb1a2 [teal]
• #fdba12 [gold]
• #f1653b [orange]
• So no other colors besides these should be used.

```html
<!DOCTYPE html>
<html lang="en">
<head>
<meta charset="utf-8">
<title>Parcelwise HQ Letterhead</title>
<link href="https://fonts.googleapis.com/css2?family=Lato:wght@300;400;700&family=Yesteryear&family=Roboto:wght@400&display=swap" rel="stylesheet">
<style>
  :root {
    --blue: #355c98;
    --teal: #1eb1a2;
    --gold: #fdba12;
    --orange: #f1653b;
    --ink: #3b3b3b;
    --paper: #ffffff;
  }
  * { margin: 0; padding: 0; box-sizing: border-box; }
  html, body { width: 996px; height: 1200px; overflow: hidden; background: var(--paper); }
  .letterhead {
    position: relative;
    width: 996px;
    height: 1200px;
    background: linear-gradient(180deg, #ffffff 0%, #f6f6f7 100%);
    font-family: "Lato", Arial, sans-serif;
    color: var(--ink);
  }
  .icon-field {
    position: absolute;
    inset: 0;
    background:
      radial-gradient(circle at 92% 24%, rgba(241,101,59,0.07) 0, transparent 70px),
      radial-gradient(circle at 80% 66%, rgba(241,101,59,0.06) 0, transparent 70px),
      radial-gradient(circle at 93% 84%, rgba(30,177,162,0.06) 0, transparent 60px),
      radial-gradient(circle at 22% 24%, rgba(253,186,18,0.07) 0, transparent 60px);
  }
  .brand {
    position: absolute;
    left: 78px;
    top: 42px;
    display: flex;
    align-items: center;
    gap: 14px;
  }
  .brand-dot {
    width: 52px; height: 52px;
    border-radius: 50%;
    border: 5px solid var(--blue);
  }
  .brand-name {
    font-weight: 300;
    font-size: 46px;
    color: var(--blue);
    letter-spacing: 0.5px;
  }
  .contact {
    position: absolute;
    left: 708px;
    top: 38px;
    padding-left: 10px;
    border-left: 1.5px solid #c9c9c9;
    font-family: "Roboto", Arial, sans-serif;
    font-size: 15px;
    line-height: 28px;
    color: var(--ink);
  }
  .contact li { list-style: none; display: flex; align-items: center; gap: 6px; }
  .contact svg { width: 15px; height: 15px; }
  .letter-body {
    position: absolute;
    left: 80px;
    top: 308px;
    width: 832px;
  }
  .salutation {
    font-weight: 700;
    font-size: 19px;
    color: var(--blue);
    margin-bottom: 26px;
  }
  .letter-body p {
    font-size: 19px;
    line-height: 31px;
    text-align: justify;
    margin-bottom: 24px;
  }
  .closing { font-size: 22px; margin-top: 34px; }
  .signature {
    font-family: "Yesteryear", cursive;
    font-size: 42px;
    color: var(--blue);
    margin-top: 2px;
  }
  .address {
    position: absolute;
    left: 80px;
    top: 1138px;
    display: flex;
    align-items: center;
    gap: 6px;
    font-family: "Roboto", Arial, sans-serif;
    font-size: 15px;
  }
  .address svg { width: 15px; height: 15px; }
  .footer-bands { position: absolute; left: 0; bottom: 0; width: 996px; height: 46px; }
  .web {
    position: absolute;
    right: 56px;
    bottom: 8px;
    font-family: "Roboto", Arial, sans-serif;
    font-size: 19px;
    letter-spacing: 3px;
    color: #ffffff;
  }
</style>
</head>
<body>
<main class="letterhead">
  <div class="icon-field" role="img" aria-label="Faint scattered line icons: lightbulb, person, lightning, pin, padlock"></div>

  <header class="brand">
    <span class="brand-dot"></span>
    <span class="brand-name">Parcelwise HQ</span>
  </header>

  <ul class="contact">
    <li><svg viewBox="0 0 16 16"><circle cx="8" cy="8" r="7" fill="none" stroke="#355c98" stroke-width="1.5"/><rect x="5.5" y="4" width="5" height="8" rx="1" fill="none" stroke="#355c98" stroke-width="1.3"/></svg>(555) 014-2290</li>
    <li><svg viewBox="0 0 16 16"><circle cx="8" cy="8" r="7" fill="none" stroke="#355c98" stroke-width="1.5"/><path d="M5 4.5c0 4 2.5 6.5 6.5 6.5l0.5-1.8-2-0.8-0.8 0.9c-1.2-0.6-2-1.4-2.6-2.6l0.9-0.8-0.8-2z" fill="#355c98"/></svg>(555) 018-4471(Main)</li>
    <li><svg viewBox="0 0 16 16"><circle cx="8" cy="8" r="7" fill="none" stroke="#355c98" stroke-width="1.5"/><rect x="4" y="5.5" width="8" height="5.5" fill="none" stroke="#355c98" stroke-width="1.2"/><path d="M4 5.5l4 3 4-3" fill="none" stroke="#355c98" stroke-width="1.2"/></svg>jlane@parcelwisehq.example</li>
  </ul>

  <section class="letter-body">
    <h2 class="salutation">Dear Mr. Lorem,</h2>
    <p>Lorem ipsum dolor sit amet, consectetuer adipiscing elit, sed diam nonummy nibh euismod tincidunt ut laoreet dolore magna aliquam erat volutpat. Ut wisi enim ad minim veniam, quis nostrud exerci tation ullamcorper suscipit lobortis nisl ut aliquip ex ea commodo consequat. Duis autem vel eum iriure dolor in hendiusto odio dignissim qui blandit praesent luptatum zzril delenit augue duis dolore te feugait nulla facilisi.</p>
    <p>Lorem ipsum dolor sit amet, consectetuer adipiscing elit, sed diam nonummy nibh euismod tincidunt ut laoreet dolore magna aliquam erat volutpat. Ut wisi enim ad minim veniam, quis nostrud exerci tation ullamcorper suscipit lobortis nisl ut aliquip ex ea commodo consequat. Duis autem vel eum iriure dolor in hendiusto odio dignissim qui blandit praesent luptatum zzril delenit augue duis dolore te feugait nulla facilisi.</p>
    <p>Lorem ipsum dolor sit amet, consectetuer adipiscing elit, sed diam nonummy nibh euismod tincidunt ut laoreet dolore magna aliquam erat volutpat. Ut wisi enim ad minim veniam, quis nostrud exerci tation ullamcorper suscipit lobortis nisl ut aliquip ex ea commodo consequat. Duis autem vel eum iriure dolor in hendiusto odio dignissim qui blandit praesent luptatum zzril delenit augue duis dolore te feugait nulla facilisi.</p>
    <div class="closing">Sincerely Your,</div>
    <div class="signature">Your Name</div>
  </section>

  <div class="address">
    <svg viewBox="0 0 16 16"><circle cx="8" cy="8" r="7" fill="none" stroke="#355c98" stroke-width="1.5"/><path d="M8 12s-3-3-3-5.2a3 3 0 0 1 6 0C11 9 8 12 8 12z" fill="none" stroke="#355c98" stroke-width="1.2"/></svg>
    42 Harbor Lane, Fieldtown, MI 40001
  </div>

  <svg class="footer-bands" viewBox="0 0 996 46" preserveAspectRatio="none" aria-hidden="true">
    <polygon points="0,22 640,22 622,46 0,46" fill="#1eb1a2"/>
    <polygon points="672,0 996,0 996,46 632,46" fill="#355c98"/>
  </svg>
  <div class="web">www.parcelwisehq.example</div>
</main>
</body>
</html>
```